A Health & Fitness Website selling saunas and Cold tubs

www.dockvaultguys.com, www.frostlanterguys, www.chillharborguys
Design a website
We are selling saunas, infrared saunas, cold plunge tubs, and massage chairs to financially successful MEN.
We want professional, simple, masculine with a touch of sexy.
One section for each… saunas, cold plunge tubs, massage chairs.
Each will have at least two buy links to their affiliate/supplier/store.
The landing page / opening page / needs big & bold; a full screen image? a great picture showing the warmth of a sauna? Need your ideas
The pictures are everything.

The Website for our book
https://maebelsvigorguys.com/

Coding

Coded - Design and coding required

Number of Pages Required

1 page

Requirements
Must have
• Great pictures

```html
<!DOCTYPE html>
<html lang="en">
<head>
<meta charset="UTF-8">
<title>Mabel Vigor Fitness for Men</title>
<link rel="stylesheet" href="https://fonts.googleapis.com/css2?family=Oswald:wght@400;500;600;700&family=Poppins:wght@400;500;600&display=swap">
<style>
:root{
  --orange:#e8541d;
  --orange-light:#f08a3c;
  --orange-deep:#c8421a;
  --ink:#111111;
  --white:#ffffff;
  --muted:#555555;
  --line:#dddddd;
  --hero-dark:#2a1710;
  --hero-warm:#8a4a2a;
}
*{box-sizing:border-box;margin:0;padding:0}
html,body{width:1200px;height:3876px;overflow:hidden;background:var(--white);font-family:"Poppins",sans-serif;color:var(--ink)}
.page{position:relative;width:1200px;height:3876px;overflow:hidden}
.abs{position:absolute}
.heading{font-family:"Oswald",sans-serif}
.btn{display:inline-block;border-radius:20px;font-size:14px;font-weight:500;padding:8px 18px;line-height:1}
.btn-solid{background:var(--orange);color:var(--white)}
.btn-outline{background:var(--white);color:var(--orange);border:1px solid var(--orange)}
.brand{display:flex;align-items:center;gap:8px;font-family:"Oswald",sans-serif;font-weight:600;font-size:20px}
.brand-dot{width:22px;height:22px;border-radius:50%;background:var(--orange)}

/* header */
.site-header{top:0;left:0;width:1200px;height:110px;background:var(--white)}
.site-header .brand{position:absolute;left:110px;top:38px;color:var(--ink)}
.site-header .btn{position:absolute;right:110px;top:34px;padding:12px 20px}

/* hero */
.hero{top:110px;left:0;width:1200px;height:720px;background:linear-gradient(100deg,var(--hero-dark) 0%,#4a2818 45%,var(--hero-warm) 75%,#c08060 100%)}
.hero-tag{left:110px;top:160px;width:420px;color:#f6b28c;font-size:19px;line-height:1.45}
.hero-title{left:110px;top:315px;width:520px;color:var(--white);font-size:40px;font-weight:600;line-height:1.2}
.hero-sub{left:110px;top:425px;width:420px;color:var(--white);font-size:12px;line-height:1.5}
.hero-wave{left:0;top:760px;width:1200px;height:100px}

/* circulation */
.circ-photo{left:110px;top:892px;width:262px;height:290px;border-radius:24px;background:linear-gradient(160deg,#3c3c3c,#7a6a5c 55%,#2a2a2a)}
.circ-title{left:635px;top:925px;width:450px;font-size:36px;font-weight:600;line-height:1.3}
.circ-sub{left:635px;top:1060px;width:450px;font-size:23px;line-height:1.45;font-family:"Oswald",sans-serif;font-weight:400}

/* products */
.products{top:1375px;left:0;width:1200px;height:605px;background:linear-gradient(120deg,var(--orange-deep),var(--orange) 45%,var(--orange-light) 100%)}
.products-title{top:62px;left:0;width:1200px;text-align:center;color:var(--white);font-size:40px;font-weight:600}
.product{top:150px;width:260px;text-align:center}
.product-photo{width:240px;height:240px;margin:0 auto;border-radius:50%;border:6px solid var(--white)}
.product-name{margin-top:26px;color:var(--white);font-size:24px;font-weight:600}
.product-actions{margin-top:14px;display:flex;justify-content:center;gap:8px}
.photo-sauna{background:linear-gradient(160deg,#c07a3a,#7a3f18)}
.photo-plunge{background:linear-gradient(160deg,#dfe8f0,#9fb4c6)}
.photo-chair{background:linear-gradient(160deg,#d9d3cc,#6a5a4a)}

/* benefits */
.benefits-col{top:2075px;list-style:none;font-size:15px;line-height:1.35}
.benefits-col li{display:flex;gap:10px;margin-bottom:16px;width:240px}
.benefits-col li::before{content:"";flex:0 0 10px;height:10px;margin-top:5px;border-radius:2px;background:var(--orange)}
.benefits-photo{left:690px;top:2085px;width:345px;height:345px;border-radius:50%;border:7px solid var(--orange);background:linear-gradient(160deg,#f3dcc4,#caa07c)}
.benefits-note{left:110px;top:2432px;width:420px;font-size:27px;font-weight:500;line-height:1.3}

/* blood flow */
.flow{top:2590px;left:0;width:1200px;height:340px;background:linear-gradient(90deg,#f3f3f3 0%,#cfcfcf 8%,#1b1b1b 30%,#0b0b0b 100%)}
.flow-people-left{top:-70px;left:0;width:380px;height:410px;background:linear-gradient(180deg,#6a5a50,#2a2220)}
.flow-people-right{top:-40px;left:940px;width:260px;height:380px;background:linear-gradient(180deg,#8a7060,#2a2220)}
.flow-title{top:70px;left:540px;width:380px;color:var(--white);font-size:40px;font-weight:600;line-height:1.4}

/* testimonials */
.testi-title{top:3018px;left:0;width:1200px;text-align:center;font-size:40px;font-weight:500}
.testi-card{top:3100px;width:268px;height:275px;border:2px solid var(--line);border-radius:14px;padding:22px 20px}
.testi-meta{display:flex;justify-content:space-between;font-size:11px;color:var(--muted)}
.stars{color:var(--orange);letter-spacing:2px;font-size:14px}
.testi-text{margin-top:16px;font-size:13px;line-height:1.5;color:#222}
.arrow{top:3222px;width:36px;height:36px;border-radius:50%;border:2px solid #999;display:flex;align-items:center;justify-content:center;color:var(--orange)}

/* footer */
.footer-curve{top:3440px;left:0;width:1200px;height:120px}
.footer{top:3520px;left:0;width:1200px;height:356px;background:var(--ink);color:var(--white)}
.footer-label{font-size:17px;font-weight:600}
.social{display:flex;gap:12px;margin-top:18px}
.social span{width:34px;height:34px;border-radius:50%;background:var(--orange)}
.footer .brand{position:absolute;left:510px;top:90px;color:var(--white)}
.subscribe-form{display:flex;margin-top:18px}
.subscribe-form .field{width:230px;height:34px;background:var(--white);color:#999;font-size:12px;padding:9px 12px}
.subscribe-form .go{width:36px;height:34px;background:var(--orange);display:flex;align-items:center;justify-content:center}
.copyright{top:298px;left:0;width:1200px;text-align:center;font-size:13px}
</style>
</head>
<body>
<div class="page">

  <header class="site-header abs">
    <div class="brand"><span class="brand-dot"></span>Mabel Vigor</div>
    <a class="btn btn-solid">Buy now</a>
  </header>

  <section class="hero abs" role="img" aria-label="Woman wrapped in a towel relaxing in a warm wooden sauna">
    <p class="hero-tag abs">Mabel Vigor Fitness for Men Top of the Line Health Products Exclusively for the Financially Successful</p>
    <h1 class="hero-title abs heading">Dramatically Improve Your Health Without Exercise</h1>
    <p class="hero-sub abs">Successful Men Recognize the Importance of Their Health and Make It a Priority. It's Your Time. You've Earned It.</p>
  </section>
  <svg class="hero-wave abs" viewBox="0 0 1200 100" preserveAspectRatio="none">
    <path d="M0 0 H1200 V30 C900 95 300 95 0 30 Z" fill="var(--orange)"/>
    <path d="M0 0 H1200 V18 C900 80 300 80 0 18 Z" fill="var(--hero-dark)"/>
  </svg>

  <div class="circ-photo abs" role="img" aria-label="Muscular man lifting dumbbells in a gym"></div>
  <h2 class="circ-title abs heading">A Mans Body Thrives on Circulation And It Doesn't Care How You Get It.</h2>
  <p class="circ-sub abs">When there's no time for exercise.<br>use Hot, Cold, or Massage.<br>The Benefits are Numerous.</p>

  <section class="products abs">
    <h2 class="products-title abs heading">Our Products</h2>
    <div class="product abs" style="left:170px">
      <div class="product-photo photo-sauna" role="img" aria-label="Wooden infrared sauna interior"></div>
      <div class="product-name heading">Infrared Saunas</div>
      <div class="product-actions"><a class="btn btn-outline">Buy now</a><a class="btn btn-outline">Buy from Order</a></div>
    </div>
    <div class="product abs" style="left:470px">
      <div class="product-photo photo-plunge" role="img" aria-label="Cold plunge tub outdoors in snow"></div>
      <div class="product-name heading">Cold Plunge Tubs</div>
      <div class="product-actions"><a class="btn btn-outline">Buy now</a><a class="btn btn-outline">Buy from Order</a></div>
    </div>
    <div class="product abs" style="left:770px">
      <div class="product-photo photo-chair" role="img" aria-label="Leather massage chair"></div>
      <div class="product-name heading">Massage Chairs</div>
      <div class="product-actions"><a class="btn btn-outline">Buy now</a><a class="btn btn-outline">Buy from Order</a></div>
    </div>
  </section>

  <ul class="benefits-col abs" style="left:110px">
    <li>Relieve Stress</li><li>Detox Your Pores</li><li>Relieve Muscle Tension</li><li>Boost Energy Levels</li><li>Increase Testosterone</li><li>Reduce Inflammation</li><li>Increase Immunity Reduce</li>
  </ul>
  <ul class="benefits-col abs" style="left:370px">
    <li>Depression</li><li>Alleviate Joint Pain</li><li>Healthier Skin</li><li>Lower the Risk of Cardiovascular Disease</li><li>Increase Metabolism</li><li>Promote Weight Loss</li><li>A Longer &amp; Healthier Life</li>
  </ul>
  <div class="benefits-photo abs" role="img" aria-label="Smiling woman in a bright room"></div>
  <p class="benefits-note abs heading">Specific Improvements will be Individual to You.</p>

  <section class="flow abs">
    <div class="flow-people-left abs" role="img" aria-label="Athletic man and woman posing together"></div>
    <div class="flow-people-right abs" role="img" aria-label="Athletic woman in workout wear"></div>
    <h2 class="flow-title abs heading">Everything Works Better with Increased Blood Flow</h2>
  </section>

  <h2 class="testi-title abs heading">Our Testimonials</h2>
  <div class="arrow abs" style="left:70px">&#8249;</div>
  <div class="testi-card abs" style="left:132px">
    <div class="testi-meta"><span class="stars">★★★★★</span><span>5 days ago</span></div>
    <p class="testi-text">"I climb in my sauna half asleep every morning for 20 minutes before I take a shower and head off to work. It's the only thing I found that really wakes me up in the morning. I'm not a coffee drinker so that's never been an option but this sauna is the perfect morning wake up."</p>
  </div>
  <div class="testi-card abs" style="left:466px">
    <div class="testi-meta"><span class="stars">★★★★★</span><span>5 days ago</span></div>
    <p class="testi-text">"I climb in my sauna half asleep every morning for 20 minutes before I take a shower and head off to work. It's the only thing I found that really wakes me up in the morning. I'm not a coffee drinker so that's never been an option but this sauna is the perfect morning wake up."</p>
  </div>
  <div class="testi-card abs" style="left:800px">
    <div class="testi-meta"><span class="stars">★★★★★</span><span>5 days ago</span></div>
    <p class="testi-text">"I climb in my sauna half asleep every morning for 20 minutes before I take a shower and head off to work. It's the only thing I found that really wakes me up in the morning. I'm not a coffee drinker so that's never been an option but this sauna is the perfect morning wake up."</p>
  </div>
  <div class="arrow abs" style="left:1094px">&#8250;</div>

  <svg class="footer-curve abs" viewBox="0 0 1200 120" preserveAspectRatio="none">
    <path d="M0 40 C300 110 900 110 1200 40 V120 H0 Z" fill="var(--orange)"/>
    <path d="M0 58 C300 125 900 125 1200 58 V120 H0 Z" fill="var(--ink)"/>
  </svg>
  <footer class="footer abs">
    <div class="abs" style="left:130px;top:110px">
      <div class="footer-label">Social Links</div>
      <div class="social"><span></span><span></span><span></span></div>
    </div>
    <div class="brand"><span class="brand-dot"></span>Mabel Vigor</div>
    <div class="abs" style="left:800px;top:110px">
      <div class="footer-label">SUBSCRIBE FOR UPDATES</div>
      <div class="subscribe-form"><div class="field">Enter email</div>
        <div class="go"><svg width="16" height="16" viewBox="0 0 16 16"><path d="M2 8h11M9 4l4 4-4 4" stroke="#fff" stroke-width="2" fill="none"/></svg></div>
      </div>
    </div>
    <p class="copyright abs">©Copyrights 2024 Company Name &nbsp;|&nbsp; All Rights Reserved</p>
  </footer>

</div>
</body>
</html>
```